New Business Cards for Tormin Group

We need a new Business Card to compliment our new logo. We are a vibrant design, manufacture and install business providing recreation areas, public parks and Municipal spaces. We want business cards that are classy, modern and clean.

We have recently changed our logo, and are celebrating our 40th anniversary. We want business cards with a new modern design to reflect our status.

Target Market(s)

Customers

Contact Information for Business Card

We need all the details of our 3 offices as per the business card attached. Please disregard the old logo on the business card, the other three files show our new logo.

Requirements
Must have
• All info as per attached business card but with new logo.
Nice to have

```html
<!DOCTYPE html>
<html lang="en">
<head>
<meta charset="utf-8">
<title>Tormin Group – Business Card</title>
<link href="https://fonts.googleapis.com/css2?family=Roboto:wght@400;500&family=Roboto+Condensed:wght@400;700&display=swap" rel="stylesheet">
<style>
  :root {
    --page: #e9e7e4;
    --card-white: #fbfbfb;
    --card-black: #0d0d0d;
    --accent: #e8404f;
    --ink-grey: #6f6f73;
    --logo-grey: #59595c;
    --text-light: #f2f2f2;
  }
  * { margin: 0; padding: 0; box-sizing: border-box; }
  html, body { width: 1200px; height: 1023px; overflow: hidden; }
  body {
    background: var(--page);
    display: flex; flex-direction: column; align-items: center; justify-content: center;
    gap: 40px;
    font-family: "Roboto Condensed", "Arial Narrow", sans-serif;
  }
  .card {
    width: 800px; height: 457px; flex: none;
    border-radius: 18px; overflow: hidden;
    box-shadow: 0 14px 32px rgba(0,0,0,.18);
    display: flex; flex-direction: column;
  }
  .card-front { background: var(--card-white); }
  .card-top {
    height: 216px; flex: none;
    display: flex; justify-content: space-between; align-items: center;
    padding: 0 52px 0 48px;
  }
  .person { align-self: flex-end; padding-bottom: 26px; }
  .person-name {
    font-family: "Roboto", sans-serif; font-weight: 500;
    font-size: 27px; color: var(--accent); letter-spacing: .4px; text-transform: uppercase;
  }
  .person-role { font-size: 17.5px; color: var(--ink-grey); margin: 1px 0 10px 2px; }
  .contact-line {
    display: flex; align-items: center; gap: 10px;
    font-size: 17px; color: var(--ink-grey); line-height: 24px;
  }
  .contact-line svg { width: 13px; height: 13px; flex: none; }
  .contact-line .hl { color: var(--accent); }
  .brand { display: flex; align-items: center; gap: 14px; }
  .brand-mark { width: 88px; height: 88px; border-radius: 50%; background: var(--accent); flex: none; }
  .brand-name {
    font-family: "Roboto Condensed", sans-serif; font-weight: 700;
    font-size: 46px; line-height: 1; color: var(--logo-grey); text-transform: uppercase; white-space: nowrap;
  }
  .divider { height: 7px; flex: none; background: var(--accent); border-bottom: 2px solid var(--card-white); }
  .card-bottom {
    flex: 1; background: var(--card-black);
    display: grid; grid-template-columns: repeat(3, 1fr);
    padding: 28px 40px 0 48px; gap: 24px;
  }
  .office-title { font-size: 25px; font-weight: 400; color: var(--accent); margin-bottom: 6px; }
  .office-line { font-size: 16px; color: var(--text-light); line-height: 22px; white-space: nowrap; }
  .office-gap { height: 16px; }
  .office-line .lbl { color: var(--accent); margin-right: 5px; }

  .card-back { background: var(--card-black); justify-content: center; }
  .back-band {
    height: 190px; background: var(--card-white);
    border-top: 5px solid var(--accent); border-bottom: 5px solid var(--accent);
    display: flex; align-items: center; justify-content: center;
  }
  .back-band .brand { gap: 20px; }
  .back-band .brand-mark { width: 110px; height: 110px; }
  .back-band .brand-name { font-size: 58px; }
</style>
</head>
<body>
  <div class="card card-front">
    <div class="card-top">
      <div class="person">
        <div class="person-name">Marek Delavan</div>
        <div class="person-role">Managing Partner</div>
        <div class="contact-line">
          <svg viewBox="0 0 16 16"><path d="M4 1l3 3-2 2c1 2 3 4 5 5l2-2 3 3-2 3C7 15 1 9 1 3z" fill="var(--accent)"/></svg>
          +971 (0)50 418 7306
        </div>
        <div class="contact-line">
          <svg viewBox="0 0 16 16"><rect x="1" y="3" width="14" height="10" fill="none" stroke="var(--accent)" stroke-width="1.6"/><path d="M1 3l7 6 7-6" fill="none" stroke="var(--accent)" stroke-width="1.6"/></svg>
          marek@tormingroup.com
        </div>
        <div class="contact-line">
          <svg viewBox="0 0 16 16"><circle cx="8" cy="8" r="6.5" fill="none" stroke="var(--accent)" stroke-width="1.5"/><ellipse cx="8" cy="8" rx="3" ry="6.5" fill="none" stroke="var(--accent)" stroke-width="1.2"/><path d="M1.5 8h13" stroke="var(--accent)" stroke-width="1.2"/></svg>
          <span>www.<span class="hl">tormingroup</span>.com</span>
        </div>
      </div>
      <div class="brand">
        <div class="brand-mark"></div>
        <div class="brand-name">Tormin Group</div>
      </div>
    </div>
    <div class="divider"></div>
    <div class="card-bottom">
      <section class="office">
        <h2 class="office-title">Head Office</h2>
        <p class="office-line">P.O. Box:</p>
        <p class="office-line">31840 Abu Dhabi, U.A.E.</p>
        <div class="office-gap"></div>
        <p class="office-line"><span class="lbl">P :</span>+971 (0)2 5718290</p>
        <p class="office-line"><span class="lbl">F :</span>+971 (0)2 5718291</p>
        <p class="office-line"><span class="lbl">E :</span>sales@tormingroup.com</p>
      </section>
      <section class="office">
        <h2 class="office-title">Dubai Office</h2>
        <p class="office-line">P.O. Box:</p>
        <p class="office-line">274106 Dubai, U.A.E.</p>
        <div class="office-gap"></div>
        <p class="office-line"><span class="lbl">P :</span>+971 (0)4 3826540</p>
        <p class="office-line"><span class="lbl">F :</span>+971 (0)4 3826541</p>
        <p class="office-line"><span class="lbl">E :</span>sales@tormingroup.com</p>
      </section>
      <section class="office">
        <h2 class="office-title">Qatar Office</h2>
        <p class="office-line">P.O. Box:</p>
        <p class="office-line">19372 Doha, Qatar</p>
        <div class="office-gap"></div>
        <p class="office-line"><span class="lbl">P :</span>+974 44718360</p>
        <p class="office-line"><span class="lbl">F :</span>+974 44718361</p>
        <p class="office-line"><span class="lbl">E :</span>sales@tormingroup.com</p>
      </section>
    </div>
  </div>

  <div class="card card-back">
    <div class="back-band">
      <div class="brand">
        <div class="brand-mark"></div>
        <div class="brand-name">Tormin Group</div>
      </div>
    </div>
  </div>
</body>
</html>
```